Modern Business Card

Modern professional business card with more than just logo and demographic info. Something memorable.

We are a trendy/modern chiropractic group with an emphasis on neurology, hence the minimalist-type brain logo. We want to convey that modern and technical aspect with professionalism and the elite nature of our practice environment.

```html
<!DOCTYPE html>
<html lang="en">
<head>
<meta charset="utf-8">
<title>Keystone Chiropractic – Business Card</title>
<link href="https://fonts.googleapis.com/css2?family=Cinzel:wght@500&family=Fjalla+One&family=Montserrat:wght@400&display=swap" rel="stylesheet">
<style>
  :root {
    --backdrop: #e9e9ea;
    --card: #1e1f21;
    --card-edge: #2a2b2e;
    --pattern-dark: #232427;
    --pattern-light: #55565a;
    --accent: #4a80c8;
    --ink: #ffffff;
    --ink-soft: #d6d6d8;
  }
  * { margin: 0; padding: 0; box-sizing: border-box; }
  html, body { width: 1200px; height: 900px; overflow: hidden; }
  body {
    background: var(--backdrop);
    font-family: "Montserrat", sans-serif;
    position: relative;
  }
  .card {
    position: absolute;
    left: 250px;
    width: 700px;
    height: 400px;
    background: var(--card);
    border: 1px solid var(--card-edge);
    overflow: hidden;
    box-shadow: 0 10px 30px rgba(0,0,0,.25);
  }
  .card--back { top: 40px; }
  .card--front { top: 460px; }

  .back-pattern {
    position: absolute;
    inset: 0;
    background: linear-gradient(90deg, var(--pattern-dark) 0%, var(--pattern-dark) 20%, var(--pattern-light) 100%);
  }
  .back-mark {
    position: absolute;
    left: 50%;
    top: 50%;
    width: 40px;
    height: 40px;
    margin: -20px 0 0 -20px;
    background: var(--accent);
  }

  .brand {
    position: absolute;
    top: 62px;
    left: 0;
    right: 0;
    display: flex;
    align-items: center;
    justify-content: center;
    gap: 18px;
  }
  .brand__square {
    width: 70px;
    height: 70px;
    background: var(--accent);
  }
  .brand__name {
    font-family: "Cinzel", serif;
    font-weight: 500;
    color: var(--ink);
    line-height: 1;
  }
  .brand__line1 { display: block; font-size: 52px; letter-spacing: 1px; }
  .brand__line2 { display: block; font-size: 27px; letter-spacing: 1.5px; margin-top: 2px; }

  .person {
    position: absolute;
    top: 216px;
    right: 360px;
    text-align: right;
  }
  .person__name {
    font-family: "Fjalla One", sans-serif;
    font-size: 38px;
    color: var(--accent);
    letter-spacing: .5px;
    line-height: 1;
  }
  .person__role {
    font-size: 19px;
    color: var(--ink-soft);
    margin-top: 6px;
  }
  .divider {
    position: absolute;
    top: 212px;
    left: 362px;
    width: 2px;
    height: 74px;
    background: var(--accent);
  }
  .contact {
    position: absolute;
    top: 210px;
    left: 392px;
    list-style: none;
  }
  .contact__item {
    display: flex;
    align-items: center;
    gap: 12px;
    font-size: 18px;
    color: var(--ink);
    line-height: 26px;
  }
  .contact__item svg { width: 15px; height: 15px; flex: none; }
  .contact__domain { color: var(--accent); }
  .address {
    position: absolute;
    bottom: 48px;
    left: 0;
    right: 0;
    text-align: center;
    font-size: 19px;
    color: var(--ink);
    letter-spacing: .5px;
  }
</style>
</head>
<body>

<section class="card card--back" aria-label="Card back">
  <div class="back-pattern" role="img" aria-label="Repeating embossed brand-mark pattern fading from dark to grey"></div>
  <div class="back-mark"></div>
</section>

<section class="card card--front" aria-label="Card front">
  <div class="brand">
    <div class="brand__square"></div>
    <div class="brand__name">
      <span class="brand__line1">KEYSTONE</span>
      <span class="brand__line2">CHIROPRACTIC</span>
    </div>
  </div>

  <div class="person">
    <div class="person__name">DANIEL MORROW</div>
    <div class="person__role">Director</div>
  </div>

  <div class="divider"></div>

  <ul class="contact">
    <li class="contact__item">
      <svg viewBox="0 0 16 16" aria-hidden="true"><path d="M4 1.5 6 4.5 4.8 6a8 8 0 0 0 5.2 5.2L11.5 10l3 2-1.2 2.5C7 14 2 9 1.5 2.7Z" fill="none" stroke="var(--accent)" stroke-width="1.4" stroke-linejoin="round"/></svg>
      (555) 214-0387
    </li>
    <li class="contact__item">
      <svg viewBox="0 0 16 16" aria-hidden="true"><rect x="1.5" y="3.5" width="13" height="9" fill="none" stroke="var(--accent)" stroke-width="1.4"/><path d="M1.5 3.5 8 9l6.5-5.5" fill="none" stroke="var(--accent)" stroke-width="1.4"/></svg>
      info@keystonechiro.com
    </li>
    <li class="contact__item">
      <svg viewBox="0 0 16 16" aria-hidden="true"><circle cx="8" cy="8" r="6.5" fill="none" stroke="var(--accent)" stroke-width="1.3"/><ellipse cx="8" cy="8" rx="3" ry="6.5" fill="none" stroke="var(--accent)" stroke-width="1.1"/><path d="M1.5 8h13M2.5 4.8h11M2.5 11.2h11" stroke="var(--accent)" stroke-width="1.1"/></svg>
      <span>www.<span class="contact__domain">keystonechiro</span>.com</span>
    </li>
  </ul>

  <p class="address">1187 Larkspur Lane Corvallis, OR 97330</p>
</section>

</body>
</html>
```